College presentation for a Venture ForgeLab - how to talk to customers

I need a simple design for a college PowerPoint/ google slide presentation for students that are going through a Venture ForgeLab. No flashy colors
- Accessible font - or provide the font - I like the orvel's website font or normal text font
- use a neutral colors schemes of grays - with 1-2 highlight colors
- You can use the photos in the presentation or others
- Urgent the presentation is on Thursday - I will award the winner on Wednesday.
- It's 23 slides long.

Target Market(s)

College students interested in startups

Industry/Entity Type

College

Font styles to use
Serif
Sans Serif
Other font styles liked:
• helvetica

Colors

Designer to choose only greyscale colors for use in the design.

Requirements
Must have
• clean , simple design neural colors like greyscale with 1-3 pop colors
Should not have
• no flashy colors, or hard to read text

```html
<!DOCTYPE html>
<html lang="en">
<head>
<meta charset="utf-8">
<title>Venture ForgeLab – Customer Development Slides</title>
<link rel="stylesheet" href="https://fonts.googleapis.com/css2?family=Archivo+Black&family=Arimo:wght@400;700&display=swap">
<style>
:root{
  --canvas:#808080;
  --ink:#ffffff;
  --black:#111111;
  --charcoal:#262626;
  --graphite:#3a3a3a;
  --blue:#12b2f0;
  --orange:#f07d1e;
  --green:#2fbf4a;
  --heavy:"Archivo Black", "Arial Black", sans-serif;
  --body:"Arimo", Helvetica, Arial, sans-serif;
}
*{box-sizing:border-box;margin:0;padding:0}
html,body{width:1200px;height:1059px;overflow:hidden;background:var(--canvas)}
body{position:relative;font-family:var(--body);color:var(--ink)}
.slide{position:absolute;width:526px;height:296px;overflow:hidden;background:var(--charcoal);box-shadow:0 6px 22px rgba(0,0,0,.45)}
.col-a{left:62px}.col-b{left:612px}
.row-1{top:62px}.row-2{top:382px}.row-3{top:701px}
.photo{position:absolute}
.abs{position:absolute}
.label{position:absolute;font-family:var(--body);font-weight:700;font-size:15px;letter-spacing:.2px;white-space:nowrap}
.heading{position:absolute;font-family:var(--heavy);font-size:21px;line-height:1.27;letter-spacing:.5px;white-space:nowrap}
.blue{color:var(--blue)}.orange{color:var(--orange)}

/* cover */
.cover .photo{inset:0;background:radial-gradient(ellipse 90px 120px at 395px 70px,#fafafa 0%,#bdbdbd 30%,#4a4a4a 70%,#2b2b2b 100%)}
.cover-tag{position:absolute;left:0;top:26px;width:314px;height:43px;background:var(--blue);font-family:var(--body);font-weight:700;font-size:25px;line-height:43px;padding-left:16px;letter-spacing:.3px}
.cover-kicker{position:absolute;left:23px;top:182px;font-family:var(--heavy);font-size:21px;color:var(--orange);letter-spacing:.4px}
.cover-title{position:absolute;left:23px;top:212px;font-weight:700;font-size:19px;line-height:28px}

/* dialogue */
.dialogue .photo{inset:0;background:linear-gradient(90deg,#555 0%,#9a9a9a 70%,#cfcfcf 100%)}
.dialogue .shape{position:absolute;inset:0}
.dialogue-lines{position:absolute;left:27px;top:147px;font-size:12px;line-height:16.5px}

/* agenda */
.agenda .photo{inset:0;background:linear-gradient(120deg,#6b6b6b 0%,#a9a9a9 45%,#5a5a5a 100%)}
.agenda .shape{position:absolute;inset:0}
.agenda-list{position:absolute;left:57px;top:147px;list-style:none;font-weight:700;font-size:12px;color:var(--ink)}
.agenda-list li{height:23px;display:flex;align-items:center;gap:10px}
.agenda-list svg{flex:none;margin-left:-17px}

/* rules */
.rules .photo{inset:0;background:linear-gradient(90deg,#1d1d1d 0%,#2e2e2e 45%,#8a8a8a 80%,#bdbdbd 100%)}
.rule{position:absolute;left:26px;display:flex;align-items:center;gap:8px;font-size:12px}
.rule svg{flex:none}

/* problem */
.problem{background:var(--black)}
.problem .photo{border-radius:50%}
.problem-lines{position:absolute;left:269px;top:148px;font-weight:700;font-size:15px;line-height:27.5px}

/* contact */
.contact .photo{inset:0;background:radial-gradient(ellipse at 60% 40%,#4a4a4a 0%,#2a2a2a 70%,#1d1d1d 100%)}
.contact .rocket{position:absolute;left:120px;top:5px;width:60px;height:290px;background:linear-gradient(180deg,#d9d9d9 0%,#9a9a9a 30%,rgba(255,255,255,.6) 100%);border-radius:30px 30px 0 0}
.contact .clouds{position:absolute;left:0;right:0;bottom:0;height:70px;background:linear-gradient(180deg,rgba(255,255,255,0) 0%,#e6e6e6 55%,#ffffff 100%)}
.contact-info{position:absolute;left:217px;top:150px;font-size:21px;line-height:28px}
</style>
</head>
<body>

<section class="slide cover col-a row-1">
  <div class="photo" role="img" aria-label="Businessman climbing stairs toward a glowing rocket-shaped doorway"></div>
  <div class="cover-tag">VENTURE FORGELAB</div>
  <div class="cover-kicker">CUSTOMER DEVELOPMENT</div>
  <div class="cover-title">Mom’s test - how to talk<br>to customers</div>
</section>

<section class="slide dialogue col-b row-1">
  <div class="photo" role="img" aria-label="Smiling young team standing in a bright office"></div>
  <svg class="shape" width="526" height="296" viewBox="0 0 526 296"><path d="M0 0H292C370 90 370 210 292 296H0Z" fill="#232323"/></svg>
  <div class="label" style="left:27px;top:35px">VENTURE FORGELAB</div>
  <div class="heading" style="left:27px;top:77px">MOM’S TEST<br><span class="blue">WHAT PEOPLE SAY</span></div>
  <div class="dialogue-lines">
    You: Mom, I have a business idea. Do you have 5 mins?<br>
    Mom: Of course, dear<br>
    You: You life your Tablio and use it a lot?<br>
    Mom: Sure it’s great.<br>
    You: Would you buy a cookbook app?<br>
    Mom: I love cookbooks, sounds nice. Does it come with<br>
    vegan recipes? Or something special for Xmas?
  </div>
</section>

<section class="slide agenda col-a row-2">
  <div class="photo" role="img" aria-label="Team meeting around a table in a loft office"></div>
  <svg class="shape" width="526" height="296" viewBox="0 0 526 296"><ellipse cx="140" cy="150" rx="124" ry="152" fill="#12b2f0" fill-opacity=".93"/></svg>
  <div class="label" style="left:424px;top:14px;line-height:20px;white-space:normal;width:100px">VENTURE<br>FORGELAB</div>
  <div class="heading orange" style="left:57px;top:63px">AGENDA</div>
  <div class="label" style="left:56px;top:108px">MOM’S TEST</div>
  <ul class="agenda-list">
    <li><svg width="13" height="10" viewBox="0 0 13 10"><path d="M1 5l4 4 7-8" fill="none" stroke="#fff" stroke-width="2.2"/></svg>What is the problem?</li>
    <li><svg width="13" height="10" viewBox="0 0 13 10"><path d="M1 5l4 4 7-8" fill="none" stroke="#fff" stroke-width="2.2"/></svg>How to talk to customers ?</li>
    <li><svg width="13" height="10" viewBox="0 0 13 10"><path d="M1 5l4 4 7-8" fill="none" stroke="#fff" stroke-width="2.2"/></svg>How to ask questions?</li>
    <li><svg width="13" height="10" viewBox="0 0 13 10"><path d="M1 5l4 4 7-8" fill="none" stroke="#fff" stroke-width="2.2"/></svg>Who to talk to?</li>
  </ul>
</section>

<section class="slide rules col-b row-2">
  <div class="photo" role="img" aria-label="Excited woman celebrating at her laptop"></div>
  <div class="label" style="left:27px;top:35px">VENTURE FORGELAB</div>
  <div class="heading" style="left:27px;top:77px">GENERAL RULE OF<br>THUMB TO WATCH FOR</div>
  <div class="rule" style="top:146px">
    <svg width="36" height="36" viewBox="0 0 36 36"><circle cx="18" cy="18" r="16.5" fill="none" stroke="#12b2f0" stroke-width="1.6"/><path d="M11 10v15h15M13 22l4-5 3 3 5-6" fill="none" stroke="#fff" stroke-width="1.5"/></svg>
    High frequency of usage</div>
  <div class="rule" style="top:193px">
    <svg width="36" height="36" viewBox="0 0 36 36"><circle cx="18" cy="18" r="16.5" fill="none" stroke="#f07d1e" stroke-width="1.6"/><path d="M20 8l-8 12h6l-2 9 8-12h-6z" fill="none" stroke="#fff" stroke-width="1.4"/></svg>
    It is urgent/painful enough</div>
  <div class="rule" style="top:240px">
    <svg width="36" height="36" viewBox="0 0 36 36"><circle cx="18" cy="18" r="16.5" fill="none" stroke="#2fbf4a" stroke-width="1.6"/><circle cx="18" cy="18" r="10" fill="none" stroke="#fff" stroke-width="1.4"/><circle cx="18" cy="15.5" r="3.3" fill="none" stroke="#fff" stroke-width="1.4"/><path d="M12 25c2-4 10-4 12 0" fill="none" stroke="#fff" stroke-width="1.4"/></svg>
    Is it worth it/ will people pay</div>
</section>

<section class="slide problem col-a row-3">
  <div class="photo" role="img" aria-label="Group of smiling colleagues in an office" style="left:41px;top:-24px;width:200px;height:200px;background:linear-gradient(160deg,#cfcfcf,#6e6e6e)"></div>
  <div class="photo" role="img" aria-label="Smiling woman working at a laptop" style="left:7px;top:116px;width:200px;height:200px;background:linear-gradient(200deg,#d8d8d8,#5c5c5c)"></div>
  <div class="label" style="left:269px;top:25px">VENTURE FORGELAB</div>
  <div class="heading blue" style="left:269px;top:95px">THE PROBLEM</div>
  <div class="problem-lines">
    People try to be nice<br>
    Therefore they lie in your face<br>
    without realizing it<br>
    Bad data it worse than no data<br>
    E.g. “I’ll definitely buy that”
  </div>
</section>

<section class="slide contact col-b row-3">
  <div class="photo" role="img" aria-label="Starry night sky"></div>
  <div class="rocket" role="img" aria-label="Rocket launching with exhaust trails"></div>
  <div class="clouds" role="img" aria-label="White clouds along the bottom"></div>
  <div class="label" style="left:217px;top:55px">VENTURE FORGELAB</div>
  <div class="heading blue" style="left:217px;top:97px">MARA VELEN</div>
  <div class="contact-info">Co-Founder Brightpath Learning<br>mara.velen@mailbox.test</div>
</section>

</body>
</html>
```